Silver Bloom Marisol's Cleaning Service Business Cards Project

A business card with all contact details with logo design on there (already have a logo) eye catching Logo and contact info on one side, full logo on the back, must target upper class residential and corporate companies, fitness companies, still keep it on the feminine side of things , must look elegant

Target Market(s)

Upper class homes and corporate companies

Industry/Entity Type

Cleaning Service

Contact Information for Business Card

Name: Marisol Quenby
Position: Director
ABN: 31647209853
Email: marisolssilvercleaning@tidymail.example
Number: 0417906354

Font styles to use
Decorative

Colors

Designer to choose colors to be used in the design.

Requirements
Must have
• Available Sydney Wide, contact info and logo on one side, full logo on the back
Nice to have
• Professional appearance
Should not have
• Cheap advert looking stuff

```html
<!DOCTYPE html>
<html lang="en">
<head>
<meta charset="utf-8">
<title>Silver Bloom Marisol's Cleaning Service – Business Cards</title>
<link rel="stylesheet" href="https://fonts.googleapis.com/css2?family=Arvo:wght@400;700&family=Open+Sans:wght@600&family=Tinos&display=swap">
<style>
  :root {
    --backdrop: #b4b4b4;
    --card: #2e3140;
    --card-pattern: #2f4a52;
    --teal: #2ee3d6;
    --teal-soft: #86f2ec;
    --ink-light: #f4f6f8;
  }
  * { box-sizing: border-box; margin: 0; padding: 0; }
  html, body {
    width: 1200px;
    height: 960px;
    overflow: hidden;
    background: var(--backdrop);
  }
  .canvas {
    position: relative;
    width: 1200px;
    height: 960px;
  }
  .card {
    position: absolute;
    width: 600px;
    height: 344px;
    background: var(--card);
    overflow: hidden;
  }
  .card--front { left: 322px; top: 108px; }
  .card--back { left: 320px; top: 493px; }

  /* faint faceted decoration (derived from the brand symbol) shown as a soft tonal field */
  .front-pattern {
    position: absolute;
    inset: 0;
    background:
      radial-gradient(ellipse 46% 52% at 50% 48%, var(--card) 55%, transparent 100%),
      linear-gradient(135deg, var(--card-pattern) 0%, var(--card) 50%, var(--card-pattern) 100%);
  }
  .contact-block {
    position: absolute;
    left: 0;
    right: 0;
    top: 108px;
    text-align: center;
    color: var(--ink-light);
    font-family: "Tinos", "Times New Roman", serif;
    font-size: 14px;
    line-height: 19px;
  }
  .contact-name {
    font-family: "Arvo", "Rockwell", serif;
    font-weight: 700;
    font-size: 19px;
    line-height: 22px;
    color: var(--teal);
    letter-spacing: 0.2px;
    text-transform: uppercase;
  }
  .contact-role {
    font-family: "Arvo", "Rockwell", serif;
    font-weight: 700;
    font-size: 13px;
    line-height: 16px;
    color: var(--teal-soft);
    letter-spacing: 1px;
    text-transform: uppercase;
    margin-top: 2px;
    margin-bottom: 17px;
  }
  .contact-abn { margin-bottom: 7px; }

  .brand {
    position: absolute;
    left: 0;
    right: 0;
    top: 0;
    height: 100%;
  }
  .brand-mark {
    position: absolute;
    left: 50%;
    top: 82px;
    width: 64px;
    height: 64px;
    margin-left: -32px;
    border-radius: 50%;
    border: 2px solid var(--teal);
  }
  .brand-name {
    position: absolute;
    left: 0;
    right: 0;
    top: 206px;
    font-family: "Arvo", "Rockwell", serif;
    font-weight: 400;
    font-size: 24px;
    line-height: 28px;
    color: var(--teal);
    text-align: center;
    text-transform: uppercase;
    letter-spacing: 0.5px;
  }
  .brand-tagline {
    position: absolute;
    left: 0;
    right: 0;
    top: 237px;
    font-family: "Open Sans", "Helvetica", sans-serif;
    font-weight: 600;
    font-size: 9px;
    line-height: 12px;
    color: var(--ink-light);
    text-align: center;
    text-transform: uppercase;
    letter-spacing: 2.6px;
  }
</style>
</head>
<body>
  <main class="canvas">
    <section class="card card--front" aria-label="Business card front">
      <div class="front-pattern" role="img" aria-label="Faint faceted-line background decoration"></div>
      <div class="contact-block">
        <p class="contact-name">Marisol Quenby</p>
        <p class="contact-role">Director</p>
        <p class="contact-abn">ABN: 31647209853</p>
        <p class="contact-phone">(P) 0417906354</p>
        <p class="contact-email">marisolssilvercleaning@tidymail.example</p>
        <p class="contact-web">www.silverbloomclean.example</p>
      </div>
    </section>

    <section class="card card--back" aria-label="Business card back">
      <div class="brand">
        <span class="brand-mark" aria-hidden="true"></span>
        <p class="brand-name">Silver Bloom</p>
        <p class="brand-tagline">Marisol's Cleaning Service</p>
      </div>
    </section>
  </main>
</body>
</html>
```